Fenwick Grading LTD - website for irrigation & Landscape Lighting & Buried service wire

Looking for a website to help promote my business with Irrigation (installation, service, etc) and buried service wire/drainage solutions.

Commercial/Residential

Landscape lighting.

I’ll get photos in the trucks and trailers to upload as well maybe the machine as well.

Target Market(s)

Homeowners who want green grass and beautiful gardens. Beautiful landscape lighting

Industry/Entity Type

Irrigation systems and landscape lighting and buried service wire to homes and offering Drainage soltions.

Coding

Coded - Design and coding required

Number of Pages Required

4 page

Colors
F0912C
F2A743
F7CA91
FBE8D2
FDF5EE

Requirements
Must have
• was hoping to link up my email on fenwickgrading@mailbox-example.net with the website if possible.
Nice to have
• Page for Irrigation, page for landscape lighting, page buried service wire & drainage soltions.

```html
<!DOCTYPE html>
<html lang="en">
<head>
<meta charset="UTF-8">
<title>Fenwick Grading LTD – Irrigation, Lighting &amp; Installation</title>
<link href="https://fonts.googleapis.com/css2?family=Playfair+Display:wght@800;900&family=Poppins:wght@400;500;600;700&display=swap" rel="stylesheet">
<style>
:root{
  --orange:#F0912C;
  --orange-2:#F2A743;
  --peach:#F7CA91;
  --cream:#FBE8D2;
  --cream-light:#FDF5EE;
  --ink:#1d1d1d;
  --text:#4a4a4a;
  --white:#ffffff;
}
*{margin:0;padding:0;box-sizing:border-box}
html,body{width:1200px;height:4420px;overflow:hidden}
body{font-family:"Poppins",sans-serif;color:var(--text);background:var(--white);position:relative}
.abs{position:absolute}

/* header */
.site-header{position:absolute;top:0;left:0;width:1200px;height:112px;background:var(--cream-light)}
.brand{position:absolute;left:140px;top:26px;display:flex;align-items:center;gap:10px}
.brand-mark{width:14px;height:14px;background:var(--orange);border-radius:50%}
.brand-name{font-family:"Poppins",sans-serif;font-weight:700;color:var(--orange);font-size:22px;line-height:24px;text-transform:uppercase}
.brand-name small{display:block;font-size:12px;line-height:16px;letter-spacing:3px}
.main-nav{position:absolute;left:430px;top:44px;display:flex;gap:22px;font-size:13px;font-weight:600;color:var(--ink);text-transform:uppercase}
.main-nav .active{color:var(--orange);position:relative}
.main-nav .active::after{content:"";position:absolute;left:50%;top:22px;width:4px;height:4px;margin-left:-2px;background:var(--orange);border-radius:50%}
.btn{display:inline-block;background:var(--orange);color:var(--ink);font-weight:600;font-size:13px;text-transform:uppercase;border-radius:30px;padding:16px 28px;letter-spacing:.5px}
.btn-contact{position:absolute;left:930px;top:28px;padding:16px 34px}

/* hero */
.hero{position:absolute;top:112px;left:0;width:1200px;height:520px}
.hero-photo{position:absolute;inset:0;background:radial-gradient(circle at 85% 35%,#c9d6a8 0%,#6f8f3a 22%,#2f4a1c 55%,#17260e 100%)}
.hero-copy{position:absolute;left:140px;top:104px;width:520px;color:var(--white)}
.hero-copy h1{font-size:31px;line-height:46px;font-weight:600}
.hero-copy h1 span{color:var(--orange);font-weight:700}
.hero-copy p{font-size:13px;line-height:21px;margin-top:18px;width:460px}
.hero-copy .btn{margin-top:24px;font-size:12px;padding:14px 24px}

/* section titles */
.section-title{position:absolute;left:0;width:1200px;text-align:center;font-family:"Playfair Display",serif;font-weight:900;font-size:30px;color:var(--ink);text-transform:uppercase;letter-spacing:.5px}
.title-rule{position:absolute;left:560px;width:80px;height:2px;background:var(--peach)}

/* feature blocks */
.feature-frame{position:absolute;border:2px solid var(--peach);border-radius:18px}
.feature-photo{position:absolute;border-radius:18px}
.feature-copy{position:absolute;width:440px}
.eyebrow{color:var(--orange);font-weight:700;font-size:26px;text-transform:uppercase;line-height:34px}
.feature-copy h3{color:var(--ink);font-weight:600;font-size:22px;line-height:32px;margin-top:6px}
.feature-copy p{font-size:15px;line-height:25px;margin-top:16px}
.feature-copy .btn{margin-top:26px;font-size:12px;padding:14px 26px}

.wave-band{position:absolute;left:0;width:1200px}

/* testimonials */
.testimonials{position:absolute;left:110px;top:3430px;width:980px;display:flex;justify-content:space-between}
.review{width:300px;background:var(--white);border-radius:16px;padding:70px 20px 24px;text-align:center;position:relative;box-shadow:0 6px 20px rgba(240,145,44,.12)}
.avatar{position:absolute;left:110px;top:-48px;width:80px;height:80px;border-radius:50%;background:linear-gradient(160deg,#8c7a6b,#3b3029);border:4px solid var(--white)}
.review p{font-size:14px;line-height:22px}
.review h4{color:var(--orange);font-size:14px;font-weight:600;text-transform:uppercase;margin-top:18px}
.review span{font-size:12px;color:var(--text)}
.dots{position:absolute;left:528px;top:3784px;display:flex;gap:14px;align-items:center}
.dots i{width:12px;height:12px;border-radius:50%;background:var(--peach);display:block}
.dots i.on{width:20px;height:20px;border:3px solid var(--orange);background:var(--orange-2)}

/* footer */
.site-footer{position:absolute;left:0;top:4040px;width:1200px;height:348px;background:var(--cream-light)}
.footer-brand{position:absolute;left:140px;top:40px}
.footer-brand .brand-name{font-size:30px;line-height:32px}
.footer-brand .brand-name small{font-size:14px}
.footer-about{position:absolute;left:140px;top:140px;width:320px;font-size:14px;line-height:22px}
.socials{position:absolute;left:140px;top:226px;display:flex;gap:12px}
.socials i{display:block;width:30px;height:30px;border-radius:50%;border:2px solid var(--orange)}
.footer-col{position:absolute;top:70px}
.footer-col h5{color:var(--orange);font-size:26px;font-weight:600;margin-bottom:14px}
.footer-col li{list-style:none;font-size:14px;line-height:20px;margin-bottom:14px;color:var(--ink)}
.contact-item{display:flex;gap:12px;align-items:flex-start}
.contact-item svg{flex:none;margin-top:2px}
.copyright{position:absolute;left:140px;top:4396px;font-size:12px;color:var(--ink)}
.legal{position:absolute;left:790px;top:4396px;font-size:12px;color:var(--ink);display:flex;gap:24px;text-transform:uppercase}
.bottom-bar{position:absolute;left:0;top:4388px;width:1200px;height:32px;background:var(--orange)}
</style>
</head>
<body>

<header class="site-header">
  <div class="brand">
    <span class="brand-mark"></span>
    <div class="brand-name">Fenwick<small>Grading LTD</small></div>
  </div>
  <nav class="main-nav">
    <span class="active">Home</span>
    <span>Irrigation</span>
    <span>Landscape Lighting</span>
    <span>Fiber Optic Installation</span>
  </nav>
  <span class="btn btn-contact">Contact</span>
</header>

<section class="hero">
  <div class="hero-photo" role="img" aria-label="Watering can sprinkling water over green garden plants"></div>
  <div class="hero-copy">
    <h1>Transform Your Outdoor Space with Our Expert <span>IRRIGATION</span> and <span>LIGHTING</span> Solutions</h1>
    <p>Get the perfect blend of form and function with our state-of-the-art irrigation systems and landscape lighting. Trust our experienced team to deliver top-notch fiber optic installation for your home.</p>
    <span class="btn">Get a Free Quote</span>
  </div>
</section>

<!-- irrigation -->
<div class="title-rule" style="top:712px"></div>
<h2 class="section-title" style="top:714px">Irrigation Systems</h2>
<div class="feature-frame" style="left:156px;top:812px;width:420px;height:500px"></div>
<div class="feature-photo" role="img" aria-label="Lawn sprinkler spraying water across green grass" style="left:172px;top:828px;width:428px;height:500px;background:linear-gradient(160deg,#a9c8d8 0%,#6f9a4a 45%,#3f6a22 100%)"></div>
<div class="feature-copy" style="left:668px;top:900px">
  <div class="eyebrow">Efficient and Effective</div>
  <h3>Watering Solutions for Your<br>Lawn and Garden</h3>
  <p>Our irrigation systems are designed to provide your lawn and garden with the right amount of water, without wasting a single drop. With our expert installation and service, you can rest assured that your plants will receive the nourishment they need to thrive.</p>
  <span class="btn">Learn More</span>
</div>

<!-- landscape lighting band -->
<svg class="wave-band" style="top:1340px" width="1200" height="1030" viewBox="0 0 1200 1030" aria-hidden="true">
  <path d="M0 70 C300 0 600 110 900 50 C1050 20 1130 30 1200 40 L1200 960 C900 1040 600 930 300 990 C180 1010 80 1000 0 980 Z" fill="#FDF5EE"/>
</svg>
<div class="title-rule" style="top:1602px"></div>
<h2 class="section-title" style="top:1604px">Landscape Lighting</h2>
<div class="feature-copy" style="left:140px;top:1780px;width:430px">
  <div class="eyebrow">Enhance Your Outdoor</div>
  <h3>Space with Beautiful and Functional<br>Lighting Solutions</h3>
  <p>Our landscape lighting solutions are designed to enhance the beauty and functionality of your outdoor space. From subtle pathway lighting to dramatic spotlights, we'll work with you to create a lighting plan that meets your needs and complements your landscape.</p>
  <span class="btn">Learn More</span>
</div>
<div class="feature-frame" style="left:624px;top:1696px;width:452px;height:500px"></div>
<div class="feature-photo" role="img" aria-label="Garden lantern post among flowers and trees" style="left:608px;top:1712px;width:452px;height:496px;background:linear-gradient(160deg,#9fb87a 0%,#5a7d36 50%,#6b4a2e 100%)"></div>

<!-- fiber optic -->
<div class="title-rule" style="top:2466px"></div>
<h2 class="section-title" style="top:2468px">Fiber Optic Installation</h2>
<div class="feature-frame" style="left:156px;top:2564px;width:420px;height:500px"></div>
<div class="feature-photo" role="img" aria-label="Technician testing a fiber optic cable with a meter" style="left:172px;top:2580px;width:428px;height:500px;background:linear-gradient(150deg,#c89a6a 0%,#8a5a32 50%,#3a2416 100%)"></div>
<div class="feature-copy" style="left:668px;top:2650px">
  <div class="eyebrow">Expert Installation of</div>
  <h3>Fiber Optic Networks for<br>Your Home</h3>
  <p>Our team of experienced professionals will install your fiber optic network with precision and care. We'll work with you to ensure that your home is equipped with the latest technology, providing you with fast and reliable internet, TV, and voice services.</p>
  <span class="btn">Learn More</span>
</div>

<!-- testimonials band -->
<svg class="wave-band" style="top:3170px" width="1200" height="880" viewBox="0 0 1200 880" aria-hidden="true">
  <path d="M0 60 C250 0 500 90 800 40 C1000 10 1120 30 1200 50 L1200 880 L0 880 Z" fill="#FDF5EE"/>
</svg>
<div class="title-rule" style="top:3108px"></div>
<h2 class="section-title" style="top:3110px">What Our Customers Say</h2>
<div class="testimonials">
  <div class="review">
    <div class="avatar" role="img" aria-label="Customer portrait"></div>
    <p>Lorem ipsum dolor sit amet, consectetur adipiscing elit, sed do eiusmod tempor commodo viverra maecenas accumsan lacus vel facilisis.</p>
    <h4>Nolan Avery</h4>
    <span>Valley Home Owner</span>
  </div>
  <div class="review">
    <div class="avatar" role="img" aria-label="Customer portrait"></div>
    <p>Lorem ipsum dolor sit amet, consectetur adipiscing elit, sed do eiusmod tempor commodo viverra maecenas accumsan lacus vel facilisis.</p>
    <h4>Marta Quill</h4>
    <span>Garden Home Owner</span>
  </div>
  <div class="review">
    <div class="avatar" role="img" aria-label="Customer portrait"></div>
    <p>Lorem ipsum dolor sit amet, consectetur adipiscing elit, sed do eiusmod tempor commodo viverra maecenas accumsan lacus vel facilisis.</p>
    <h4>Owen Halberd</h4>
    <span>Lakeside Home Owner</span>
  </div>
</div>
<div class="dots"><i></i><i class="on"></i><i></i><i></i><i></i></div>

<footer class="site-footer">
  <div class="footer-brand">
    <div class="brand">
      <span class="brand-mark" style="width:18px;height:18px"></span>
      <div class="brand-name">Fenwick<small>Grading LTD</small></div>
    </div>
  </div>
  <p class="footer-about">Lorem ipsum dolor sit amet, consectetur adipiscing elit, sed do eiusmod tempor incididunt ut labore et dolore magna aliqua. Quis ipsum.</p>
  <div class="socials"><i></i><i></i><i></i><i></i></div>

  <div class="footer-col" style="left:590px">
    <h5>Quick Links</h5>
    <ul><li>Home</li><li>Irrigation</li><li>Landscape Lighting</li><li>Fiber Optic Installation</li><li>Contact</li></ul>
  </div>
  <div class="footer-col" style="left:830px;width:260px">
    <h5>Contact Info</h5>
    <ul>
      <li class="contact-item"><svg width="16" height="18" viewBox="0 0 16 18"><path d="M8 1a6 6 0 0 0-6 6c0 4.5 6 10 6 10s6-5.5 6-10a6 6 0 0 0-6-6z" fill="none" stroke="#F0912C" stroke-width="1.6"/><circle cx="8" cy="7" r="2" fill="#F0912C"/></svg><span>Address 1, Address 2, Address 3, Address 4</span></li>
      <li class="contact-item"><svg width="16" height="16" viewBox="0 0 16 16"><path d="M3 1h3l1.5 4-2 1.2a9 9 0 0 0 4.3 4.3L11 8.5l4 1.5v3a2 2 0 0 1-2 2A13 13 0 0 1 1 3a2 2 0 0 1 2-2z" fill="none" stroke="#F0912C" stroke-width="1.5"/></svg><span>1029384756</span></li>
      <li class="contact-item"><svg width="16" height="14" viewBox="0 0 16 14"><rect x="1" y="1" width="14" height="12" rx="2" fill="none" stroke="#F0912C" stroke-width="1.5"/><path d="M1.5 2l6.5 6 6.5-6" fill="none" stroke="#F0912C" stroke-width="1.5"/></svg><span style="font-size:12px">fenwickgrading@mailbox-example.net</span></li>
    </ul>
  </div>
</footer>

<div class="bottom-bar"></div>
<div class="copyright">©2024 FenwickGrading. All Rights Reserved.</div>
<div class="legal"><span>Privacy Terms</span><span>Terms &amp; Conditions</span></div>

</body>
</html>
```